elegant beautiful Hang tag for a novelty makeup towel

It's a black hand towel in the shape of a little black dress. it is called PETAL CHARM TOWEL, it is a CLEAN SLATE MAKEUP TOWEL. (doesn't show our makeup stains) Made in USA

Target Market(s)

ALL Women , Makeup artists, novelty THIS WILL BE IN THE HALVERGATE STORES AND KESTRELMOOR STORES.

Industry/Entity Type

Makeup

Contact Information for Business Card

I actually need a hang tag for a homemade handmade towel. I have a logo that I want on the tag and know what we want to say on it, on back needs to say "The essential to every girl's wardrobe. So when the little black dress comes off, our PETAL CHARM TOWEL is there to help you wash your day away. Include website www.petalcharmtowel.com OH INCLUDE TM (trademark sign next to logo please. Also, in small print on back from the makers of THE ORIGINAL CLEAN SLATE MAKEUP TOWEL. handmade in USA. also CLEAN SLATE MAKEUP TOWEL IN big font on front under logo sign with light colored pink lips after 'CLEAN SLATE" but have no idea about fonts, graphics, placement or design. Want it classy, elegant, girly! COLORS LIGHT BEIGER BACKGROUND WITH BLACK WRITING/ DESIGNS

Font styles to use
Serif
Decorative
Script

Colors
fff3d1

Requirements
Must have
• Black cream girly , also state in big writing that it's a " clean slate makeup towel" with a tiny light pink lip between the show and makeup. Include www.petalcharmtowel.com Brightwater Fenn, LLC
Nice to have
• Perhaps an outline of a little black dress. A black scroll edge of some sort around card. Classy

```html
<!DOCTYPE html>
<html lang="en">
<head>
<meta charset="utf-8">
<title>Petal Charm Towel – Hang Tag</title>
<link rel="stylesheet" href="https://fonts.googleapis.com/css2?family=Josefin+Sans:wght@300;400&family=Dancing+Script:wght@700&family=Mali:ital,wght@0,400;1,400&family=Lato:wght@700;900&family=Crimson+Text:wght@400;700&family=Open+Sans:ital,wght@1,400&display=swap">
<style>
  :root {
    --backdrop: #1c1b1b;
    --cream: #fff3d1;
    --ink: #121212;
    --lace-light: #303030;
    --lace-dark: #141414;
    --lip-pink: #f2a99a;
  }
  * { margin: 0; padding: 0; box-sizing: border-box; }
  html, body {
    width: 1200px; height: 1198px; overflow: hidden;
    background: var(--backdrop);
  }
  .canvas { position: relative; width: 1200px; height: 1198px; }
  .tag {
    position: absolute; left: 108px;
    width: 984px; height: 384px;
  }
  .tag--front { top: 170px; }
  .tag--back { top: 628px; }
  .tag-shape { position: absolute; inset: 0; width: 984px; height: 384px; }
  .tag-text {
    position: absolute; left: 0; width: 100%;
    text-align: center; color: var(--cream); white-space: nowrap;
  }

  /* front */
  .brand-name {
    top: 132px;
    font-family: "Josefin Sans", sans-serif; font-weight: 300;
    font-size: 33px; letter-spacing: 6px;
  }
  .tagline-rule {
    position: absolute; top: 190px; left: 40px; width: 916px; height: 1px;
    background: var(--cream);
  }
  .tagline {
    top: 180px; left: 50%; width: auto; transform: translateX(-50%);
    padding: 0 8px; background: #1f1f1f;
    font-family: "Open Sans", sans-serif; font-style: italic;
    font-size: 14px; letter-spacing: 0.5px;
  }
  .product-title {
    font-family: "Dancing Script", cursive; font-weight: 700;
    font-size: 44px; line-height: 1;
  }
  .product-title--first { top: 238px; }
  .product-title--second { top: 286px; }
  .lips {
    position: absolute; top: 256px; left: 596px; width: 20px; height: 11px;
  }

  /* back */
  .story {
    top: 44px;
    font-family: "Mali", cursive; font-style: italic;
    font-size: 18.5px; line-height: 28px; letter-spacing: 2px;
  }
  .website {
    top: 206px;
    font-family: "Lato", sans-serif; font-weight: 900; font-size: 26px;
  }
  .makers {
    top: 264px;
    font-family: "Crimson Text", serif; font-size: 16px; line-height: 26px;
  }
  .makers strong { font-weight: 700; }
  .origin {
    top: 336px;
    font-family: "Mali", cursive; font-style: italic;
    font-size: 17px; letter-spacing: 2px;
  }
</style>
</head>
<body>
<main class="canvas">

  <section class="tag tag--front" aria-label="Hang tag front">
    <svg class="tag-shape" viewBox="-492 -192 984 384" xmlns="http://www.w3.org/2000/svg">
      <defs>
        <radialGradient id="lace-front" cx="0" cy="0" r="480" gradientUnits="userSpaceOnUse">
          <stop offset="0" stop-color="#2e2e2e"/>
          <stop offset="1" stop-color="#161616"/>
        </radialGradient>
        <path id="wrapper-outline-front" d="M -300,-105 C -200,-210 200,-210 300,-105 C 340,-80 380,-110 420,-120 C 490,-130 490,130 420,120 C 380,110 340,80 300,105 C 200,210 -200,210 -300,105 C -340,80 -380,110 -420,120 C -490,130 -490,-130 -420,-120 C -380,-110 -340,-80 -300,-105 Z"/>
      </defs>
      <ellipse cx="0" cy="0" rx="492" ry="192" fill="var(--cream)"/>
      <use href="#wrapper-outline-front" fill="url(#lace-front)" role="img" aria-label="Black lace and paisley pattern panel"/>
      <use href="#wrapper-outline-front" transform="scale(0.965 0.93)" fill="none" stroke="var(--cream)" stroke-width="5" stroke-linecap="round" stroke-dasharray="0 14"/>
    </svg>
    <p class="tag-text brand-name">PETAL CHARM TOWEL</p>
    <div class="tagline-rule"></div>
    <p class="tag-text tagline">WASH YOUR DAY AWAY</p>
    <p class="tag-text product-title product-title--first">Clean Slate&nbsp;&nbsp;</p>
    <svg class="lips" viewBox="0 0 20 11" role="img" aria-label="Light pink lips">
      <ellipse cx="10" cy="5.5" rx="10" ry="5.5" fill="var(--lip-pink)"/>
    </svg>
    <p class="tag-text product-title product-title--second">Makeup Towel</p>
  </section>

  <section class="tag tag--back" aria-label="Hang tag back">
    <svg class="tag-shape" viewBox="-492 -192 984 384" xmlns="http://www.w3.org/2000/svg">
      <defs>
        <radialGradient id="lace-back" cx="0" cy="0" r="480" gradientUnits="userSpaceOnUse">
          <stop offset="0" stop-color="#2e2e2e"/>
          <stop offset="1" stop-color="#161616"/>
        </radialGradient>
        <path id="wrapper-outline-back" d="M -300,-105 C -200,-210 200,-210 300,-105 C 340,-80 380,-110 420,-120 C 490,-130 490,130 420,120 C 380,110 340,80 300,105 C 200,210 -200,210 -300,105 C -340,80 -380,110 -420,120 C -490,130 -490,-130 -420,-120 C -380,-110 -340,-80 -300,-105 Z"/>
      </defs>
      <ellipse cx="0" cy="0" rx="492" ry="192" fill="var(--cream)"/>
      <use href="#wrapper-outline-back" fill="url(#lace-back)" role="img" aria-label="Black lace and paisley pattern panel"/>
      <use href="#wrapper-outline-back" transform="scale(0.965 0.93)" fill="none" stroke="var(--cream)" stroke-width="5" stroke-linecap="round" stroke-dasharray="0 14"/>
    </svg>
    <p class="tag-text story">The essential<br>to every girl's wardrobe.<br>So when the little black dress comes off,<br>our PETAL CHARM TOWEL<br>is there to help you wash your day away.</p>
    <p class="tag-text website">www.petalcharmtowel.com</p>
    <p class="tag-text makers"><strong>from the makers of the original</strong><br>CLEAN SLATE MAKEUP TOWEL</p>
    <p class="tag-text origin">handmade in USA</p>
  </section>

</main>
</body>
</html>
```